Stationery Design + Business Cards

Stationary (letterhead as A4 210x297mm and Letter 8.5"x11", preferably both master page + 2nd pages)

Also need business cards, standard size 50x88mm, can be vertical or horizontal.

You can use a front/back design for the business cards, or front only.

Looking at the uploaded file (devank, you already have that), I want it to use the first logo on the list (4 colors).

Alternative, try the grayscale version (second file).

I need the following information on the business card (in no particular order, let me know what you come up with): 

Firstname Lastlame 
Title 

Mobile +1 555-204-7391 

VelaMorn, Inc. 
24851 Birchwood Ridge Passage 
Ashvale, ZN 46099 
Tel. +1 555-368-4172 
Fax +1 555-619-0834 

Web: www.velamorn.example 
Twitter: twitter/VelaMorn or @VelaMorn 
Facebook: facebook.com/VelaMorn 

For letterhead, just the company name, address + phone number & fax number 

If you think the phone/fax or something else should not be on the business cards, or something could be missing, let me know.

```html
<!DOCTYPE html>
<html lang="en">
<head>
<meta charset="utf-8">
<title>VelaMorn Business Cards</title>
<link rel="stylesheet" href="https://fonts.googleapis.com/css2?family=Source+Sans+3:wght@400;600;700&display=swap">
<style>
  :root {
    --stage: #000000;
    --paper: #ffffff;
    --band-grey: #d1d2d4;
    --band-blue: #0d4ea3;
    --brand-blue: #1b4fa0;
    --brand-dot: #f07a1f;
    --ink-grey: #4d4d4f;
    --ink-light: #ffffff;
  }
  * { margin: 0; padding: 0; box-sizing: border-box; }
  html, body { width: 1200px; height: 900px; overflow: hidden; background: var(--stage); }
  body { font-family: "Source Sans 3", Arial, sans-serif; position: relative; }

  .board-label {
    position: absolute; color: var(--ink-light); font-weight: 700; font-size: 18.5px;
    text-align: center; width: 520px; line-height: 22px;
  }

  .card { position: absolute; background: var(--paper); overflow: hidden; }
  .band { position: absolute; left: 0; width: 100%; }
  .band--grey { background: var(--band-grey); }
  .band--blue { background: var(--band-blue); }

  .brand { position: absolute; display: flex; align-items: center; gap: 9px; }
  .brand__dot { width: 32px; height: 32px; border-radius: 50%; background: var(--brand-dot); }
  .brand__name { color: var(--brand-blue); font-weight: 400; font-size: 35px; line-height: 1; letter-spacing: -0.3px; }

  .identity { position: absolute; left: 0; width: 100%; text-align: center; color: var(--ink-light); }
  .identity__name { font-weight: 700; font-size: 18.5px; line-height: 19px; }
  .identity__title { font-weight: 400; font-size: 13.5px; line-height: 17px; }
  .identity__mobile { font-weight: 700; font-size: 13.5px; line-height: 17px; }

  .contact { position: absolute; color: var(--ink-grey); font-weight: 600; font-size: 11px; line-height: 13.5px; }
  .contact--right { text-align: right; }
  .contact--center { left: 0; width: 100%; text-align: center; }
  .contact__gap { height: 8px; }
  .divider { position: absolute; width: 1px; background: var(--ink-grey); }

  .card--vertical .identity__name { font-size: 17.5px; }
  .card--vertical .contact--address { font-size: 13.5px; line-height: 17.2px; }
  .card--vertical .contact--web { font-size: 11.5px; line-height: 15px; }
</style>
</head>
<body>

  <div class="board-label" style="left:84px; top:121px;">Horizontal B. card Front Only</div>
  <div class="card card--horizontal" style="left:91px; top:149px; width:514px; height:292px;">
    <div class="band band--grey" style="top:95px; height:26px;"></div>
    <div class="band band--blue" style="top:121px; height:80px;"></div>
    <div class="band band--grey" style="top:201px; height:91px;"></div>

    <div class="brand" style="right:30px; top:36px;">
      <span class="brand__dot"></span>
      <span class="brand__name">VelaMorn</span>
    </div>

    <div class="identity" style="top:137px;">
      <div class="identity__name">Firstname Lastname</div>
      <div class="identity__title">Title</div>
      <div class="identity__mobile">Mobile +1 555-204-7391</div>
    </div>

    <div class="contact contact--right" style="right:271px; top:230px;">
      <div>Web: www.velamorn.example</div>
      <div>Twitter: twitter/VelaMorn or @VelaMorn</div>
      <div>Facebook: facebook.com/VelaMorn</div>
    </div>
    <div class="divider" style="left:257px; top:224px; height:54px;"></div>
    <div class="contact" style="left:271px; top:223px;">
      <div>VelaMorn, Inc.</div>
      <div>24851 Birchwood Ridge Passage</div>
      <div>Ashvale, ZN 46099</div>
      <div>Tel. +1 555-368-4172, Fax +1 555-619-0834</div>
    </div>
  </div>

  <div class="board-label" style="left:83px; top:488px;">Horizontal B. card Front Only</div>
  <div class="card card--horizontal" style="left:90px; top:512px; width:514px; height:292px;">
    <div class="band band--grey" style="top:95px; height:17px;"></div>
    <div class="band band--blue" style="top:112px; height:80px;"></div>
    <div class="band band--grey" style="top:192px; height:100px;"></div>

    <div class="brand" style="right:30px; top:36px;">
      <span class="brand__dot"></span>
      <span class="brand__name">VelaMorn</span>
    </div>

    <div class="identity" style="top:129px;">
      <div class="identity__name">Firstname Lastname</div>
      <div class="identity__title">Title</div>
      <div class="identity__mobile">Mobile +1 555-204-7391</div>
    </div>

    <div class="contact contact--center" style="top:205px; font-size:10.5px; line-height:14px;">
      <div>VelaMorn, Inc.</div>
      <div>24851 Birchwood Ridge Passage, Ashvale, ZN 46099</div>
      <div>Tel. +1 555-368-4172, Fax +1 555-619-0834</div>
      <div class="contact__gap"></div>
      <div>Web: www.velamorn.example</div>
      <div>Twitter: twitter/VelaMorn or @VelaMorn&nbsp;&nbsp;Facebook: facebook.com/VelaMorn</div>
    </div>
  </div>

  <div class="board-label" style="left:702px; top:181px;">Vertical B. card Front Only</div>
  <div class="card card--vertical" style="left:806px; top:212px; width:292px; height:515px;">
    <div class="band band--blue" style="top:198px; height:127px;"></div>
    <div class="band band--grey" style="top:325px; height:190px;"></div>

    <div class="brand" style="right:26px; top:143px;">
      <span class="brand__dot"></span>
      <span class="brand__name">VelaMorn</span>
    </div>

    <div class="identity" style="top:236px;">
      <div class="identity__name">Firstname Lastname</div>
      <div class="identity__title">Title</div>
      <div class="identity__mobile">Mobile +1 555-204-7391</div>
    </div>

    <div class="contact contact--center contact--address" style="top:348px;">
      <div>VelaMorn, Inc.</div>
      <div>24851 Birchwood Ridge Passage</div>
      <div>Ashvale, ZN 46099</div>
      <div>Tel. +1 555-368-4172</div>
      <div>Fax +1 555-619-0834</div>
    </div>
    <div class="contact contact--center contact--web" style="top:454px;">
      <div>Web: www.velamorn.example</div>
      <div>Twitter: twitter/VelaMorn or @VelaMorn</div>
      <div>Facebook: facebook.com/VelaMorn</div>
    </div>
  </div>

</body>
</html>
```